Talvane Aerial webdesign: Innovative Drones service company in agriculture

We need a new website according the following conditions:
• Main colour orange and current logo;
• Transparent – open – trustworthy – dynamic - personal;
• Use the smartness and overview characteristics of the crow (Talvane is Latin for crow);
• Accessible to multiple target groups and markets:
o So not too horticultural, too green;
• Use contradictions:
o Future versus nostalgia;
o Smartness crow versus precision hummingbird;
o Technology versus mechanical;
• Kestrand 2.4 LTX as a style icon?
• Long pager website
Updates

Website menu o Home o Crop monitoring  Applications Growth | Stress | Development | Diseases  Markets Breeding | Young plant | Potplants | Cutflowers | Vegetables | Soft fruit  Customer cases o Technology Aerial data collection | Artificial intelligence | Free data sets o About Vision | Company | Partners | Team | Career o Contact o News&downloads Logo: www.talvaneaerial-example.com

Target Market(s)

agriculture: owners, crop managers
oil&gas: maintenance, quality control managers and purchase managers
logistics: ware house managers, purchase managers

Industry/Entity Type

Agribusiness

Number of Pages Required

2 page

Colors
f78f20

Requirements
Must have
• long pager website
downloads
social profile
Should not have
• Not too 'green' because first impression of designers of agriculture/horticulture is using the green colour. But that is not necessary.

Keep in mind that the current logo will be updates: the circle will be more 'general' and less 'agri'. Also the green colors in the logo will be slightly darker to make it more powerful.

```html
<!DOCTYPE html>
<html lang="en">
<head>
<meta charset="utf-8">
<title>Talvane Aerial – Markets</title>
<link href="https://fonts.googleapis.com/css2?family=Lato:wght@300;400;700;900&display=swap" rel="stylesheet">
<style>
:root{
  --orange:#f78f20;
  --title:#f0902c;
  --text:#8a8a8a;
  --nav:#4a4a4a;
  --footer:#6b6b6b;
  --white:#ffffff;
}
*{box-sizing:border-box;margin:0;padding:0}
html,body{width:1200px;height:3125px;overflow:hidden;background:var(--white)}
body{position:relative;font-family:'Lato',sans-serif;color:var(--text)}
.brand{position:absolute;left:62px;top:32px;display:flex;align-items:center;gap:12px}
.brand-dot{width:44px;height:44px;border-radius:50%;background:var(--orange)}
.brand-name{font-family:'Lato',sans-serif;font-weight:400;font-size:26px;color:var(--orange);letter-spacing:.5px}
.nav{position:absolute;top:47px;left:0;width:1200px;height:14px}
.nav a{position:absolute;font-size:12.5px;font-weight:700;color:var(--nav);text-decoration:none;letter-spacing:.1px}
.intro{position:absolute;left:133px;top:118px;width:915px}
h1,h2{font-weight:300;color:var(--title)}
h1{font-size:39px;line-height:48px;margin-bottom:16px}
p{font-size:17.6px;line-height:22.5px;font-weight:300}
.intro p+p{margin-top:22px}
.market{position:absolute;width:440px}
.market h2{font-size:38px;line-height:44px;height:44px}
.market .photo{display:block;width:437px;height:290px;margin-top:6px}
.market .body{margin-top:32px}
.market .body p+p{margin-top:22px}
.footer{position:absolute;left:63px;top:2841px;width:1068px;height:284px;background:var(--footer);color:var(--white);z-index:2}
.footer h3{font-size:18.5px;font-weight:700;letter-spacing:.8px;line-height:22px}
.footer ul{list-style:none;font-size:14.5px;line-height:18px;letter-spacing:.6px;margin-top:2px}
.fcol{position:absolute}
.visit{left:76px;top:24px}
.visit address{font-style:normal;font-size:14.5px;line-height:18px;letter-spacing:.6px;margin-top:24px}
.social{position:absolute;left:84px;top:167px;width:40px;height:40px;border-radius:50%;background:var(--white)}
</style>
</head>
<body>
<header>
  <div class="brand"><span class="brand-dot"></span><span class="brand-name">Talvane Aerial</span></div>
  <nav class="nav">
    <a style="left:281px">HOME</a>
    <a style="left:349px">CROP MONITORING</a>
    <a style="left:506px">MARKETS</a>
    <a style="left:596px">CUSTOMER CASES</a>
    <a style="left:731px">TECHNOLOGY</a>
    <a style="left:843px">ABOUT</a>
    <a style="left:910px">CONTACTS</a>
    <a style="left:1000px">NEW &amp; DOWNLOADS</a>
  </nav>
</header>

<section class="intro">
  <h1>Markets</h1>
  <p>Lorem ipsum dolor sit amet, consectetur adipiscing elit. Morbi ultricies molestie orci. Aenean purus mauris, sodales nec diam dignissim, porttitor laoreet enim. Aliquam id sollicitudin turpis. Vivamus aliquet elit sem, et ornare ex aliquam in. In cursus, felis non pretium molestie, tellus lacus facilisis metus, ut accumsan nisi nulla accumsan risus. Etiam id pharetra ante. Nunc sit amet ante id justo consequat tempor. Nullam pretium arcu eu hendrerit aliquam. Sed in purus eros.</p>
  <p>Fusce placerat risus sit amet lectus egestas, pretium porttitor nisi facilisis. Morbi pellentesque odio et nulla interdum viverra. Nam suscipit, eros ut vulputate ultrices, libero odio mollis justo, nec varius felis odio ut mi. Sed felis nisl, congue at finibus in, porttitor ut elit. Etiam et mattis ipsum. Praesent vel molestie mi. Duis in nunc nunc. Class aptent taciti sociosqu ad litora torquent per conubia nostra, per inceptos himenaeos. Cras eget leo urna.</p>
</section>

<article class="market" style="left:133px;top:460px">
  <h2>Breeding</h2>
  <svg class="photo" role="img" aria-label="Plant cuttings in test tubes in a lab rack"><defs><linearGradient id="g1" x1="0" y1="0" x2="1" y2="1"><stop offset="0" stop-color="#c9cfc4"/><stop offset=".5" stop-color="#8fb36a"/><stop offset="1" stop-color="#b8b2a8"/></linearGradient></defs><rect width="437" height="290" fill="url(#g1)"/></svg>
  <div class="body"><p>Pellentesque sit amet tristique elit. Aliquam semper ultricies nulla nec molestie. Nulla facilisi. Cum sociis natoque penatibus et magnis dis parturient montes, nascetur ridiculus mus. Morbi ut eros vitae purus hendrerit efficitur eget et nulla. Ut tincidunt sit amet mauris eu tempor. Curabitur ornare vitae sem nec tempus. Morbi laoreet metus neque, eu hendrerit magna interdum a. Aliquam erat volutpat. Nam auctor ut augue eu varius. Cras elementum accumsan pellentesque. Mauris nec nisi id ante faucibus consectetur. Aenean ornare aliquet neque, a fermentum odio vulputate sed. Morbi congue purus finibus ex cursus, euismod sagittis leo ornare.</p></div>
</article>

<article class="market" style="left:610px;top:460px">
  <h2>Young Plants</h2>
  <svg class="photo" role="img" aria-label="Rows of young seedlings in trays under purple grow light"><defs><linearGradient id="g2" x1="0" y1="0" x2="0" y2="1"><stop offset="0" stop-color="#8a2a8c"/><stop offset=".35" stop-color="#7fae3c"/><stop offset="1" stop-color="#3b3128"/></linearGradient></defs><rect width="437" height="290" fill="url(#g2)"/></svg>
  <div class="body"><p>Integer maximus, leo ac ornare scelerisque, arcu mauris vulputate ex, id condimentum dolor augue sit amet nunc. Vestibulum maximus dapibus luctus. Etiam et dui ante. Phasellus malesuada nunc sit amet dui consequat, in faucibus sapien laoreet. Duis ac arcu quis elit ullamcorper rutrum vitae id dolor. Nunc feugiat nunc sit amet efficitur egestas. Morbi nec velit lorem.</p><p>Duis eget nunc luctus, mattis quam vitae, posuere ipsum. Suspendisse interdum pretium velit, nec venenatis leo fringilla in. Pellentesque ut molestie velit. Etiam maximus, velit vel mattis congue, sapien libero convallis lacus, at sollicitudin magna ligula vitae quam. Maecenas id ante ac ex tincidunt sodales.</p></div>
</article>

<article class="market" style="left:134px;top:1202px">
  <h2>Pot Plants</h2>
  <svg class="photo" role="img" aria-label="Three small seedlings in peat pots on a wooden board"><defs><linearGradient id="g3" x1="0" y1="0" x2="0" y2="1"><stop offset="0" stop-color="#ececec"/><stop offset=".55" stop-color="#8a6a52"/><stop offset="1" stop-color="#d8b08a"/></linearGradient></defs><rect width="437" height="290" fill="url(#g3)"/></svg>
  <div class="body"><p>Lorem ipsum dolor sit amet, consectetur adipiscing elit. Morbi ultricies molestie orci. Aenean purus mauris, sodales nec diam dignissim, porttitor laoreet enim. Aliquam id sollicitudin turpis. Vivamus aliquet elit sem, et ornare ex aliquam in. In cursus, felis non pretium molestie, tellus lacus facilisis metus, ut accumsan nisi nulla accumsan risus. Etiam id pharetra ante. Nunc sit amet ante id justo consequat tempor. Nullam pretium arcu eu hendrerit aliquam. Sed in purus eros.</p><p>Fusce placerat risus sit amet lectus egestas, pretium porttitor nisi facilisis. Morbi pellentesque odio et nulla interdum viverra. Nam suscipit, eros ut vulputate ultrices, libero odio mollis justo, nec varius felis odio ut mi. Sed felis nisl, congue at finibus in, porttitor ut elit. Etiam et mattis ipsum. Praesent vel molestie mi. Duis in nunc nunc. Class aptent taciti sociosqu ad litora torquent per conubia nostra, per inceptos himenaeos. Cras eget leo urna.</p></div>
</article>

<article class="market" style="left:611px;top:1202px">
  <h2>Cut Flowers</h2>
  <svg class="photo" role="img" aria-label="Collage of cut flowers in pink, red and yellow"><defs><linearGradient id="g4" x1="0" y1="0" x2="1" y2="1"><stop offset="0" stop-color="#7a5c8a"/><stop offset=".4" stop-color="#e88aa0"/><stop offset=".7" stop-color="#d8352e"/><stop offset="1" stop-color="#4a7a3a"/></linearGradient></defs><rect width="437" height="290" fill="url(#g4)"/></svg>
  <div class="body"><p>Quisque egestas feugiat turpis, vel sagittis dui finibus molestie. Morbi non ante id dui rhoncus consectetur. Maecenas malesuada libero lorem, quis feugiat mauris semper non. Maecenas a lobortis nisl. Praesent vitae vulputate lorem. Quisque pretium tristique euismod. Proin eget vehicula sapien.</p><p>Integer maximus, leo ac ornare scelerisque, arcu mauris vulputate ex, id condimentum dolor augue sit amet nunc. Vestibulum maximus dapibus luctus. Etiam et dui ante. Phasellus malesuada nunc sit amet dui consequat, in faucibus sapien laoreet. Duis ac arcu quis elit ullamcorper rutrum vitae id dolor. Nunc feugiat nunc sit amet efficitur egestas. Morbi nec velit lorem. Duis eget nunc luctus, mattis quam vitae, posuere ipsum. Suspendisse interdum pretium velit, nec venenatis leo fringilla in. Pellentesque ut molestie velit. Etiam maximus, velit vel mattis congue, sapien libero convallis lacus, at sollicitudin magna ligula vitae quam. Maecenas id ante ac ex tincidunt sodales.</p></div>
</article>

<article class="market" style="left:133px;top:2054px">
  <h2>Vegetables</h2>
  <svg class="photo" role="img" aria-label="Vegetable garden with a wooden path between planted beds"><defs><linearGradient id="g5" x1="0" y1="0" x2="1" y2="1"><stop offset="0" stop-color="#4f7a2e"/><stop offset=".5" stop-color="#9aa06a"/><stop offset="1" stop-color="#3c6a26"/></linearGradient></defs><rect width="437" height="290" fill="url(#g5)"/></svg>
  <div class="body"><p>Lorem ipsum dolor sit amet, consectetur adipiscing elit. Morbi ultricies molestie orci. Aenean purus mauris, sodales nec diam dignissim, porttitor laoreet enim. Aliquam id sollicitudin turpis. Vivamus aliquet elit sem, et ornare ex aliquam in. In cursus, felis non pretium molestie, tellus lacus facilisis metus, ut accumsan nisi nulla accumsan risus. Etiam id pharetra ante. Nunc sit amet ante id justo consequat tempor. Nullam pretium arcu eu hendrerit aliquam. Sed in purus eros.</p><p>Fusce placerat risus sit amet lectus egestas, pretium porttitor nisi facilisis. Morbi pellentesque odio et nulla interdum viverra. Nam suscipit, eros ut vulputate ultrices, libero odio mollis justo, nec varius felis odio ut mi. Sed felis nisl, congue at finibus in, porttitor ut elit.</p></div>
</article>

<article class="market" style="left:611px;top:2054px">
  <h2>Soft Fruits</h2>
  <svg class="photo" role="img" aria-label="Pile of berries, apples and citrus fruit on a light grey background"><defs><radialGradient id="g6" cx=".5" cy=".6" r=".5"><stop offset="0" stop-color="#d8452e"/><stop offset=".45" stop-color="#c2553a"/><stop offset="1" stop-color="#e4e4e4"/></radialGradient></defs><rect width="437" height="290" fill="url(#g6)"/></svg>
  <div class="body"><p>Quisque egestas feugiat turpis, vel sagittis dui finibus molestie. Morbi non ante id dui rhoncus consectetur. Maecenas malesuada libero lorem, quis feugiat mauris semper non. Maecenas a lobortis nisl. Praesent vitae vulputate lorem. Quisque pretium tristique euismod. Proin eget vehicula sapien.</p><p>Integer maximus, leo ac ornare scelerisque, arcu mauris vulputate ex, id condimentum dolor augue sit amet nunc. Vestibulum maximus dapibus luctus. Etiam et dui ante. Phasellus malesuada nunc sit amet dui consequat, in faucibus sapien laoreet. Duis ac arcu quis elit ullamcorper rutrum vitae id dolor. Nunc feugiat nunc sit amet efficitur egestas. Morbi nec velit lorem. Duis eget nunc luctus, mattis quam vitae, posuere ipsum. Suspendisse interdum pretium velit, nec venenatis leo fringilla in. Pellentesque ut molestie velit. Etiam maximus, velit vel mattis congue.</p></div>
</article>

<footer class="footer">
  <div class="fcol visit">
    <h3>WHY DON’T YOU DROP BY?</h3>
    <address>Veldhoeklaan 14B,<br>4821KP, Arnsveld<br>Email: info@talvaneaerial-example.com<br>Telephone: +31 6 00000000</address>
  </div>
  <span class="social" role="img" aria-label="Social profile"></span>
  <div class="fcol" style="left:417px;top:22px"><h3>CROP MONITORING</h3><ul><li>Growth</li><li>Stress</li><li>Development</li><li>Diseases</li></ul></div>
  <div class="fcol" style="left:417px;top:148px"><h3>MARKETS</h3><ul><li>Breeding</li><li>Young plant</li><li>Potplants</li><li>Cutflowers</li><li>Vegetables</li><li>Soft fruit</li></ul></div>
  <div class="fcol" style="left:627px;top:22px"><h3>TECHNOLOGY</h3><ul><li>Aerial data collection</li><li>Artificial intelligence</li><li>Free data sets</li></ul></div>
  <div class="fcol" style="left:627px;top:148px"><h3>NEWS &amp; DOWNLOADS</h3></div>
  <div class="fcol" style="left:627px;top:199px"><h3>CUSTOMER CASES</h3></div>
  <div class="fcol" style="left:868px;top:22px"><h3>ABOUT</h3><ul><li>Vision</li><li>Company</li><li>Partners</li><li>Team</li><li>Career</li></ul></div>
  <div class="fcol" style="left:868px;top:148px"><h3>FREE DATA SETS</h3></div>
  <div class="fcol" style="left:868px;top:199px"><h3>CONTACT</h3></div>
</footer>
</body>
</html>
```